Nimbo31.com.au Website and company image design

We are looking for an exceptional website designer / company to work with our new Australian Hosting Company

Nimbo31 is a new Cloud Hosting company launching in Australia that provides Scalable, On Demand computing resources to the Australian Market Place. Scalable, On Demand ocmputing is a nice way of saying fully scalable / redundant Virtual Private Server.

We require a full company image to be developed along with a Logo and Website. There is scope for ongoing development (preferred) for the successful candidate.

Website developement will require extensive jQuery ability (sliders for ordering etc (see: http://www.hostrivo.com.au/virtual-dedicated-servers/253/kelp_vps.html).

Please communicate directly with me to establish full website scope and request further documentation / content.

Target Market(s)

Website Designers, programmers, technicians and large companies

Industry/Entity Type

It Company

Requirements
Must have
• Slider ordering system such as http://www.hostrivo.com.au/virtual-dedicated-servers/253/kelp_vps.html

Nice to have
• CMS backend system
Should not have
• Should NOT be a monster template copy!!!

```html
<!DOCTYPE html>
<html lang="en">
<head>
<meta charset="utf-8">
<title>Nimbo31.com.au — Cloud Hosting</title>
<link rel="stylesheet" href="https://fonts.googleapis.com/css2?family=Roboto+Condensed:wght@300;400;700&family=Arimo:wght@400&family=Crimson+Pro:wght@400&display=swap">
<style>
  :root {
    --plum-deep: #2a1826;
    --plum: #32202f;
    --plum-nav: #3a2737;
    --plum-band: #24141f;
    --footer: #2b1a28;
    --footer-deep: #1f111b;
    --paper: #ece6dd;
    --paper-light: #f6f2ec;
    --red: #b31c12;
    --red-dark: #6b0f0f;
    --red-bright: #e3231c;
    --gold: #e6b84a;
    --yellow: #ffe51a;
    --ink: #222;
    --body-text: #555;
    --hero-text: #c9bcc6;
    --nav-text: #f1eaf0;
    --blue-icon: #5c82c8;
    --red-icon: #d2504a;
  }
  * { box-sizing: border-box; margin: 0; padding: 0; }
  html, body { width: 1190px; height: 1200px; overflow: hidden; }
  body { position: relative; background: var(--footer-deep); font-family: "Arimo", Arial, sans-serif; }
  .abs { position: absolute; }
  .cond { font-family: "Roboto Condensed", "Arial Narrow", sans-serif; }

  /* Header */
  .header { left: 0; top: 0; width: 1190px; height: 104px; background: linear-gradient(#3a2636, var(--plum-deep)); }
  .brand { left: 144px; top: 22px; display: flex; align-items: center; gap: 12px; }
  .brand-mark { width: 44px; height: 44px; border-radius: 50%; border: 2px solid #e9e2e8; }
  .brand-name { font-family: "Roboto Condensed", sans-serif; font-weight: 700; font-size: 36px; color: #fff; }
  .call { right: 139px; top: 36px; color: var(--gold); font-size: 16px; }

  /* Navigation */
  .nav { left: 0; top: 104px; width: 1190px; height: 73px; background: var(--plum-nav);
         border-top: 1px dashed #5a4657; border-bottom: 1px dashed #5a4657; }
  .nav ul { list-style: none; display: flex; position: absolute; left: 159px; top: 26px; gap: 0; }
  .nav li { font-family: "Roboto Condensed", sans-serif; font-size: 16px; color: var(--nav-text); margin-right: 45px; text-transform: uppercase; }
  .nav li.active { color: var(--yellow); }

  /* Hero */
  .hero { left: 0; top: 177px; width: 1190px; height: 255px; background: var(--plum); }
  .hero-title { left: 137px; top: 200px; font-family: "Roboto Condensed", sans-serif; font-weight: 300; font-size: 34px; color: #d8cdd6; }
  .hero-copy { left: 140px; top: 256px; width: 510px; font-size: 11.5px; line-height: 20px; color: var(--hero-text); }
  .hero-copy p + p { margin-top: 18px; }
  .cms-band { left: 0; top: 432px; width: 1190px; height: 93px; background: var(--plum-band); border-top: 1px solid #3f2d3c; }
  .cms { top: 463px; width: 43px; height: 43px; border-radius: 50%; background: #cfcfcf; border: 3px solid #e8e8e8; box-shadow: 0 0 0 3px #3a2837; }

  /* Price card */
  .price { left: 689px; top: 216px; width: 335px; height: 250px; background: linear-gradient(#f8f0e2 0, #f4e8d2 50%, #f8dea8 100%); border: 1px solid #d8c7a8; }
  .price-head { left: 0; top: 0; width: 100%; height: 50px; border-bottom: 1px dashed #e0cfb0; padding: 10px 0 0 20px;
                font-family: "Roboto Condensed", sans-serif; font-size: 22px; color: #2a2a2a; }
  .price-mid { left: 0; top: 50px; width: 100%; height: 130px; border-bottom: 1px dashed #e0cfb0; text-align: center;
               font-family: "Roboto Condensed", sans-serif; color: var(--red); }
  .price-mid .cur { font-size: 48px; vertical-align: 28px; margin-right: 8px; }
  .price-mid .amt { font-size: 94px; line-height: 126px; }
  .seal { left: 987px; top: 184px; width: 62px; height: 62px; border-radius: 50%; background: #e79a2a; border: 4px solid #c56a14; }
  .btn { display: flex; align-items: center; justify-content: space-between; color: #fff;
         font-family: "Roboto Condensed", sans-serif; border-radius: 22px;
         background: linear-gradient(#f0463a, var(--red-bright) 50%, #c5140f); box-shadow: 0 0 0 6px rgba(120,110,100,.35); }
  .btn-order { left: 739px; top: 452px; width: 236px; height: 40px; padding: 0 20px 0 22px; font-size: 16px; text-transform: uppercase; }

  /* Why section */
  .why { left: 0; top: 525px; width: 1190px; height: 482px; background: var(--paper); border-top: 1px dashed #c9c0b6; }
  .why-title { left: 139px; top: 558px; font-family: "Roboto Condensed", sans-serif; font-size: 29px; color: var(--red); }
  .rule { left: 302px; top: 580px; width: 748px; height: 5px; background: repeating-linear-gradient(45deg, #cfc7bd 0 1px, transparent 1px 3px); }
  .col { font-size: 11.5px; line-height: 20.5px; color: var(--body-text); }
  .col h3 { font-family: "Roboto Condensed", sans-serif; font-weight: 400; font-size: 15px; color: var(--red); margin-bottom: 8px; }
  .col a { color: var(--red-dark); text-decoration: none; }
  .col ul { list-style: none; margin-top: 8px; }
  .col li { color: var(--red-dark); line-height: 26px; padding-left: 18px; position: relative; font-size: 12px; }
  .col li::before { content: ""; position: absolute; left: 0; top: 8px; width: 11px; height: 11px; border-radius: 50%; background: var(--red-dark); }
  .col-about { left: 140px; top: 607px; width: 240px; }
  .col-about .more { display: block; margin-top: 5px; font-size: 11.5px; }
  .col-vps { left: 462px; top: 609px; width: 250px; }
  .col-ded { left: 798px; top: 608px; width: 250px; }

  .banner { left: 156px; top: 779px; width: 878px; height: 81px; background: var(--paper-light); border: 1px solid #ddd6cc; }
  .banner-text { left: 176px; top: 798px; font-family: "Roboto Condensed", sans-serif; font-weight: 300; font-size: 29px; color: var(--ink); }
  .btn-view { left: 777px; top: 798px; width: 193px; height: 42px; padding: 0 22px; font-size: 19px; }

  .quick { top: 894px; width: 58px; height: 58px; border-radius: 50%; border: 4px solid #f3efe9; box-shadow: 0 0 0 2px #d8d0c6; display: flex; align-items: center; justify-content: center; }
  .quick.blue { background: var(--blue-icon); }
  .quick.red { background: var(--red-icon); }
  .dots { top: 922px; width: 78px; height: 4px; background: repeating-linear-gradient(45deg, #c9c0b6 0 1px, transparent 1px 3px); }
  .quick-label { top: 962px; width: 160px; text-align: center; font-family: "Crimson Pro", Georgia, serif; font-size: 19px; color: var(--ink); }

  /* Footer */
  .footer { left: 0; top: 1007px; width: 1190px; height: 155px; background: var(--footer); }
  .fcol { top: 1021px; font-size: 11.5px; color: #e6dde4; }
  .fcol h4 { font-family: "Roboto Condensed", sans-serif; font-weight: 400; font-size: 14px; color: var(--gold); margin-bottom: 8px; }
  .fcol li { list-style: none; line-height: 21.5px; }
  .fcol h4.light { font-weight: 300; }
  .social { top: 1047px; width: 30px; height: 30px; border-radius: 50%; background: var(--yellow); }
</style>
</head>
<body>
  <header class="abs header"></header>
  <div class="abs brand">
    <span class="brand-mark"></span>
    <span class="brand-name">Nimbo31</span>
  </div>
  <div class="abs call cond">Call Us : +1 555 0142</div>

  <nav class="abs nav">
    <ul>
      <li class="active">Home</li>
      <li>Cloud Hosting</li>
      <li>VPS Hosting</li>
      <li>Hosting Services</li>
      <li>About</li>
      <li>Contact Us</li>
    </ul>
  </nav>

  <section class="abs hero"></section>
  <h1 class="abs hero-title">Some caption comehe here</h1>
  <div class="abs hero-copy">
    <p>Lorem Ipsum is simply dummy text of the printing and typesetting industry. Lorem Ipsum has been the industry's standard dummy text ever since the 1500s,</p>
    <p>Lorem Ipsum is simply dummy text of the printing and typesetting industry. Lorem Ipsum has been the industry's standard dummy text ever since the 1500s,</p>
  </div>

  <div class="abs cms-band"></div>
  <span class="abs cms" style="left:144px"></span>
  <span class="abs cms" style="left:204px"></span>
  <span class="abs cms" style="left:265px"></span>
  <span class="abs cms" style="left:327px"></span>

  <div class="abs price">
    <div class="abs price-head">Starting at</div>
    <div class="abs price-mid"><span class="cur">$</span><span class="amt">99</span></div>
  </div>
  <span class="abs seal" role="img" aria-label="Money back guarantee seal"></span>
  <div class="abs btn btn-order">
    <span>Submit your order</span>
    <svg width="18" height="18" viewBox="0 0 18 18"><circle cx="9" cy="9" r="7.5" fill="none" stroke="#fff" stroke-width="2"/><path d="M5 9h7M9 6l3 3-3 3" fill="none" stroke="#fff" stroke-width="2"/></svg>
  </div>

  <section class="abs why"></section>
  <h2 class="abs why-title">Why Nimbo 31</h2>
  <div class="abs rule"></div>

  <div class="abs col col-about">
    <p>Lorem Ipsum is simply dummy text of the printing and typesetting industry. Lorem Ipsum has been the industry's standard dummy text ever since the 1500s, when an unknown printer took a galley of type...</p>
    <a class="more" href="#">More about us...</a>
  </div>
  <div class="abs col col-vps">
    <h3>VPS Hosting</h3>
    <p>Lorem Ipsum is simply dummy text of the printing and typesetting industry. Lorem Ipsum has been the industry...</p>
    <ul>
      <li>4 to 40 times faster than traditional VPS</li>
      <li>Guaranteed access to resources</li>
    </ul>
  </div>
  <div class="abs col col-ded">
    <h3>Dedicated Server</h3>
    <p>Lorem Ipsum is simply dummy text of the printing and typesetting industry. Lorem Ipsum has been the industry...</p>
    <ul>
      <li>Build Dedicated Servers</li>
      <li>Compare &amp; Order Dedicated Servers</li>
    </ul>
  </div>

  <div class="abs banner"></div>
  <div class="abs banner-text">Technically Superior Cloud VPS Hosting Packages!</div>
  <div class="abs btn btn-view">
    <span>View Details...</span>
    <svg width="18" height="18" viewBox="0 0 18 18"><circle cx="9" cy="9" r="7.5" fill="none" stroke="#fff" stroke-width="2"/><path d="M5 9h7M9 6l3 3-3 3" fill="none" stroke="#fff" stroke-width="2"/></svg>
  </div>

  <div class="abs quick blue" style="left:659px">
    <svg width="30" height="30" viewBox="0 0 30 30"><circle cx="15" cy="15" r="12" fill="none" stroke="#fff" stroke-width="2"/><path d="M10 9c-1 3 3 10 9 12l2-2-3-2-1 1c-2-1-4-3-5-5l1-1-2-3z" fill="#fff"/></svg>
  </div>
  <div class="abs dots" style="left:725px"></div>
  <div class="abs quick red" style="left:815px">
    <svg width="28" height="26" viewBox="0 0 28 26"><rect x="2" y="2" width="24" height="22" fill="none" stroke="#fff" stroke-width="2"/><path d="M6 9h16M6 14h16M6 19h16" stroke="#fff" stroke-width="2"/></svg>
  </div>
  <div class="abs dots" style="left:886px"></div>
  <div class="abs quick blue" style="left:972px">
    <svg width="30" height="22" viewBox="0 0 30 22"><rect x="2" y="2" width="26" height="18" fill="none" stroke="#fff" stroke-width="2"/><path d="M2 2l13 11 13-11M2 20l10-9M28 20l-10-9" fill="none" stroke="#fff" stroke-width="2"/></svg>
  </div>
  <div class="abs quick-label" style="left:608px">+1 555 0142</div>
  <div class="abs quick-label" style="left:765px">Client Area</div>
  <div class="abs quick-label" style="left:922px">Contact us</div>

  <footer class="abs footer"></footer>
  <div class="abs fcol" style="left:140px">
    <h4>Services</h4>
    <ul><li>Cloud Hosting</li><li>VPS Hosting</li><li>Sub links</li><li>Sub links</li></ul>
  </div>
  <div class="abs fcol" style="left:368px">
    <h4>Company</h4>
    <ul><li>Home</li><li>About</li><li>Services</li><li>Order Now</li><li>Contact us</li></ul>
  </div>
  <div class="abs fcol" style="left:596px">
    <h4>Help</h4>
    <ul><li>+1 555 0142 7</li><li>maild comes here</li></ul>
  </div>
  <div class="abs fcol" style="left:824px">
    <h4 class="light">Connect with us</h4>
  </div>
  <span class="abs social" style="left:823px"></span>
  <span class="abs social" style="left:864px"></span>
</body>
</html>
```